Small legal and financial translation company needs Squarespace website, brochure and logo

Hello,
We are Lumarin Services (www.lumarinservices-example.com), a boutique legal and financial translation company. We offer our services mainly to Spanish customers. Our primary line of business is the translation of financial statements, but we translate a wide variety legal and financial texts.
The project we are offering comprises three parts: a redo of the current website, an informational brochure for potential customer and a logo design. These three parts should provide a consistent image. We would develop content soon.
We are looking for a website that would look like a typical law firm website, nothing too fancy. Right now, it is in English, Spanish and French, although the new site need only be in English and Spanish. There must be good toggling between the English and Spanish versions. There would be no need for tie-ins to social media and it would not contain a blog. Basically, a static site. We aren't interesting in driving traffic to the site or SEO, as we will contact nearly all potential customers beforehand. The website must be built in Squarespace to enable a smooth transition. The content would be similar to the current page, we'll be working on the exact content, but a rough draft is attached.
The brochure will be some three pages and would introduce the company to potential customers, using similar images as the website and the logo to be designed.
The only specifications for the logo is, as the website and brochure, it convey a sense of security and trust.
Feel free to ask with any questions as this is the first time we have used this platform.
Thank you!
Updates

I've added a more or less final version for the text in the brochure and updated the brief. Added Wednesday, June 10, 2015

Target Market(s)

Spanish law firms, auditors, accountants, banks, investment firms

Industry/Entity Type

Finance

Logo Text

Lumarin Services

Number of Pages Required

5+ page

Font styles to use
Serif

Requirements
Must have
• The website must be built in Squarespace and have a good option to toggle between English and Spanish versions.
• Brochure must be in both English and Spanish, I'm attaching a rough draft of the information that it will probably have. This should give an idea about what to include and the spacing. I will update it to include the final information.
Nice to have
• Would be nice to have some quality finance- and legal-related images
Should not have
• Vibrant colours

```html
<!DOCTYPE html>
<html lang="es">
<head>
<meta charset="utf-8">
<title>Lumarin Services — Quienes Somos</title>
<link rel="stylesheet" href="https://fonts.googleapis.com/css2?family=Montserrat:wght@400;700&family=EB+Garamond:wght@400&family=Oswald:wght@400&display=swap">
<style>
:root{
  --page-bg:#e5e5e5;
  --hero-dark:#2a2a2a;
  --hero-mid:#6b6b6b;
  --hero-light:#b9b9b9;
  --white:#ffffff;
  --brand-sky:#a9dcef;
  --teal:#3aa3a8;
  --teal-deep:#2f6f78;
  --teal-nav:#3f8ea0;
  --body-text:#505050;
  --nav-grey:#8d8d8d;
  --tile-text:#1f7f8e;
  --footer-top:#2f2f2f;
  --footer-bottom:#1e1e1e;
}
*{margin:0;padding:0;box-sizing:border-box}
html,body{width:1129px;height:1200px;overflow:hidden;background:var(--page-bg)}
body{position:relative;font-family:"EB Garamond",Georgia,serif}

.hero{position:absolute;left:0;top:0;width:1129px;height:417px;overflow:hidden}
.hero-photo{position:absolute;inset:0;
  background:
    linear-gradient(100deg,var(--hero-dark) 0%,var(--hero-mid) 22%,var(--hero-light) 42%,#8c8c8c 55%,#4a4a4a 70%,#9a9a9a 82%,#5a5a5a 100%);}
.brand{position:absolute;left:16px;top:22px;font-family:"EB Garamond",Georgia,serif;font-size:22px;color:var(--brand-sky);letter-spacing:1px}
.lang-nav{position:absolute;right:19px;top:51px;display:flex;gap:27px;list-style:none}
.lang-nav a{font-family:Montserrat,Arial,sans-serif;font-size:10.5px;font-weight:700;letter-spacing:1.6px;color:var(--white);text-decoration:none}
.hero-title{position:absolute;left:0;right:0;top:186px;text-align:center;font-family:Montserrat,Arial,sans-serif;font-weight:700;font-size:52px;letter-spacing:3px;color:var(--white)}

.side-nav{position:absolute;left:170px;top:494px}
.side-nav .section{font-size:19px;color:var(--teal-deep);margin-bottom:9px}
.side-nav ul{list-style:none}
.side-nav li{font-family:Oswald,"Arial Narrow",sans-serif;font-size:13.5px;letter-spacing:1.8px;color:var(--nav-grey);height:31px;line-height:20px}
.side-nav li.active{color:var(--teal-nav)}

.content{position:absolute;left:379px;top:494px;width:576px}
.content h1{font-weight:400;font-size:29px;color:var(--teal);margin-bottom:14px}
.content p{font-size:16px;line-height:20.2px;letter-spacing:1.35px;color:var(--body-text);text-align:justify}

.facts{position:absolute;left:379px;top:765px;display:flex;gap:10.5px}
.fact{position:relative;width:185px;height:121px;overflow:hidden}
.fact-photo{position:absolute;inset:0}
.fact:nth-child(1) .fact-photo{background:linear-gradient(160deg,#cfcfcf,#7a7a7a 60%,#2e2e2e)}
.fact:nth-child(2) .fact-photo{background:linear-gradient(180deg,#6d6d6d,#c4c4c4 55%,#3a3a3a)}
.fact:nth-child(3) .fact-photo{background:linear-gradient(200deg,#e0e0e0,#8a8a8a 55%,#2b2b2b)}
.fact-band{position:absolute;left:0;right:0;top:40px;height:50px;background:rgba(255,255,255,.72);text-align:center;color:#2b2b2b}
.fact-band strong{display:block;font-weight:400;font-size:21px;line-height:22px;color:var(--tile-text);margin-top:5px}
.fact-band span{display:block;font-size:10.5px;line-height:11.5px}
.fact:nth-child(2) .fact-band{top:30px;height:64px}
.fact:nth-child(2) .fact-band strong{margin-top:1px;margin-bottom:3px}

.footer-top{position:absolute;left:0;top:1105px;width:1129px;height:52px;background:var(--footer-top)}
.footer-bottom{position:absolute;left:0;top:1157px;width:1129px;height:43px;background:var(--footer-bottom)}
</style>
</head>
<body>
<header class="hero">
  <div class="hero-photo" role="img" aria-label="Black and white upward view of glass office towers"></div>
  <div class="brand">Lumarin Services</div>
  <ul class="lang-nav">
    <li><a href="#">HOME</a></li>
    <li><a href="#">ENGLISH</a></li>
    <li><a href="#">SPANISH</a></li>
  </ul>
  <h2 class="hero-title">QUIENES SOMOS</h2>
</header>

<nav class="side-nav">
  <div class="section">Spanish</div>
  <ul>
    <li class="active">QUIENES SOMOS</li>
    <li>VENTAJAS</li>
    <li>LEGAL TRANSLATION</li>
    <li>FINANCIAL TRANSLATION</li>
  </ul>
</nav>

<main class="content">
  <h1>Quines Somos</h1>
  <p>Somos un pequeño grupo altamente calificado de profesionales con experiencia en la ley, los servicios financieros y de traducción que cuenta con experiencia en consultoría global y auditoría empresas, bufetes de abogados y empresas de una amplia muestra representativa de industrias. Sensible a los trabajos del mundo de las finanzas, contabilidad y derecho, somos expertos orientadas al detalle que se esfuerzan por facilitar el entendimiento entre los inversores, empresas y organizaciones internacionales:</p>
</main>

<section class="facts">
  <div class="fact">
    <div class="fact-photo" role="img" aria-label="Black and white office towers under cloudy sky"></div>
    <div class="fact-band"><strong>over 30 years</strong><span>of combined experience</span></div>
  </div>
  <div class="fact">
    <div class="fact-photo" role="img" aria-label="Black and white city street between buildings"></div>
    <div class="fact-band"><strong>serving</strong><span>Big 4 firms, leading international law firms and banks and Meridia 30 listings and blue chips</span></div>
  </div>
  <div class="fact">
    <div class="fact-photo" role="img" aria-label="Black and white skyscrapers seen from below"></div>
    <div class="fact-band"><strong>over a milion</strong><span>words translated annually</span></div>
  </div>
</section>

<footer>
  <div class="footer-top"></div>
  <div class="footer-bottom"></div>
</footer>
</body>
</html>
```